Harbor Crestline (Business Card Design)

Need business cards designed. Something modern, chic, and sleek. Mabye the back of the card should be the navy blue that is in the logo and then just the logo on the back.

Target Market(s)

Those in the hotel, office, and renovation industry

Contact Information for Business Card

1. Logo 2. Dorian Fenwick 3. CEO/Founder 4. Phone: (833) HarbCre / (833) 427-2731 5. Email: dorian@theharborcrestline.com 6. Website: www.theharborcrestline.com

Font styles to use
Other font styles liked:
• Look at the logo font and base the font for everything else off of that.

Colors
0054AA
0677BA
7BADD7
CADEEF
E8F1F8

Requirements
Must have
• Colors that are associated in the logo
Nice to have
• Sleek modern clean and chic design.

```html
<!DOCTYPE html>
<html lang="en">
<head>
<meta charset="utf-8">
<title>Harbor Crestline – Business Card</title>
<link href="https://fonts.googleapis.com/css2?family=Open+Sans:wght@400;600;700&display=swap" rel="stylesheet">
<style>
  :root {
    --navy: #0c1640;
    --navy-deep: #081033;
    --navy-light: #1b2a6b;
    --gold: #d4a73a;
    --white: #ffffff;
    --soft: #dfe4f3;
    --backdrop: #2a2b2e;
  }
  * { box-sizing: border-box; margin: 0; padding: 0; }
  html, body {
    width: 1200px; height: 780px; overflow: hidden;
    background: var(--backdrop);
    font-family: "Open Sans", Arial, sans-serif;
  }
  .sheet {
    width: 1200px; height: 780px;
    display: flex; align-items: center; justify-content: center; gap: 60px;
  }
  .card {
    position: relative;
    width: 520px; height: 297px;
    background: var(--navy);
    overflow: hidden;
    border-radius: 3px;
    box-shadow: 0 10px 30px rgba(0,0,0,.45);
  }

  /* Front */
  .brand {
    position: absolute; left: 34px; top: 32px;
    display: flex; align-items: center; gap: 10px;
  }
  .brand-square { width: 14px; height: 14px; background: var(--gold); }
  .brand-name {
    color: var(--white); font-weight: 700; font-size: 19px;
    letter-spacing: 2.5px; text-transform: uppercase;
  }
  .address {
    position: absolute; left: 34px; top: 92px;
    color: var(--soft); font-size: 12.5px; line-height: 1.55;
  }
  .contacts {
    position: absolute; left: 34px; bottom: 32px;
    list-style: none; color: var(--soft); font-size: 12.5px; line-height: 1.75;
  }
  .contacts li { display: flex; align-items: center; gap: 8px; }
  .contacts svg { width: 12px; height: 12px; flex: none; }
  .person {
    position: absolute; right: 40px; top: 34px; text-align: right;
  }
  .person-name { color: var(--gold); font-weight: 700; font-size: 24px; line-height: 1.1; }
  .person-title { color: var(--white); font-size: 13px; margin-top: 4px; }
  .gold-tab {
    position: absolute; right: 0; top: 38px;
    width: 16px; height: 46px; background: var(--gold);
  }
  .front-feature {
    position: absolute; right: 28px; bottom: 22px;
    width: 170px; height: 150px;
    background: linear-gradient(135deg, var(--navy-deep) 0%, var(--navy-light) 65%, #6e6fa8 100%);
    opacity: .85;
  }

  /* Back */
  .back-field {
    position: absolute; inset: 0;
    background: radial-gradient(ellipse at 85% 80%, #34428a 0%, var(--navy-light) 30%, var(--navy) 70%);
  }
  .back .brand {
    left: 50%; top: 50%; transform: translate(-50%, -50%);
    gap: 14px;
  }
  .back .brand-square { width: 20px; height: 20px; }
  .back .brand-name { font-size: 28px; letter-spacing: 4px; }
</style>
</head>
<body>
<main class="sheet">
  <section class="card front" aria-label="Card front">
    <div class="brand">
      <span class="brand-square"></span>
      <span class="brand-name">Harbor Crestline</span>
    </div>
    <p class="address">4120 Linden Park Dr<br>Suite 210, Easton, MD 21601</p>
    <ul class="contacts">
      <li>
        <svg viewBox="0 0 24 24" fill="var(--gold)"><path d="M6.6 10.8a15 15 0 0 0 6.6 6.6l2.2-2.2a1 1 0 0 1 1-.25 11.4 11.4 0 0 0 3.6.57 1 1 0 0 1 1 1V20a1 1 0 0 1-1 1A17 17 0 0 1 3 4a1 1 0 0 1 1-1h3.5a1 1 0 0 1 1 1c0 1.25.2 2.45.57 3.57a1 1 0 0 1-.25 1z"/></svg>
        (833) HarbCre / (833) 427-2731
      </li>
      <li>
        <svg viewBox="0 0 24 24" fill="none" stroke="var(--gold)" stroke-width="2"><circle cx="12" cy="12" r="9"/><path d="M3 12h18M12 3c3 3.5 3 14.5 0 18M12 3c-3 3.5-3 14.5 0 18"/></svg>
        www.theharborcrestline.com
      </li>
      <li>
        <svg viewBox="0 0 24 24" fill="none" stroke="var(--gold)" stroke-width="2"><rect x="3" y="5" width="18" height="14" rx="1"/><path d="M3 6l9 7 9-7"/></svg>
        dorian@theharborcrestline.com
      </li>
    </ul>
    <div class="person">
      <p class="person-name">Dorian Fenwick</p>
      <p class="person-title">CEO/Founder</p>
    </div>
    <span class="gold-tab"></span>
    <div class="front-feature" role="img" aria-label="Large embossed brand emblem decoration"></div>
  </section>

  <section class="card back" aria-label="Card back">
    <div class="back-field" role="img" aria-label="Repeating brand emblem pattern fading to a glossy highlight"></div>
    <div class="brand">
      <span class="brand-square"></span>
      <span class="brand-name">Harbor Crestline</span>
    </div>
  </section>
</main>
</body>
</html>
```